IT Company that provides secure IT solutions and services to our customers

We need business cards and a logo for a new IT Solutions company just created based in Kuala Lumpur, Malaysia. But will also be serving other countries in the region. We provide secure data, voice solutions on mobile platforms. Our first offering is encrypted voice and data solutions for IOS, Android, Windows and BlackBerry devices.

Target Market(s)

large organizations Govt, Police, Defence, Anti-corruption, Legal, highly regulated industries such as Health-care, Financial, Banking, Insurance,

Industry/Entity Type

Information Technology

Contact Information for Business Card

VelmoraNet (Logo - colour is ORVEX blue)Roshan Adeel Managing Director Kryption IT Sdn. Bhd.5th Floor, Block D, Wisma PLB,No.14 Jalan Seri Melor,50470, Kuala LumpurMalaysia

Font styles to use
Sans Serif

Colors
3176b5
ec1f27
fbed22

Requirements
Must have
• VelmoraNet all in Blue like ORVEX blue. A logo design perhaps a play of VN, K with a dangling T (colour can be any)
Nice to have
• I want a clean crisp card, not too busy, easy to read.

```html
<!DOCTYPE html>
<html lang="en">
<head>
<meta charset="utf-8">
<title>VelmoraNet Business Card</title>
<link href="https://fonts.googleapis.com/css2?family=Montserrat:wght@600;700&family=Questrial&display=swap" rel="stylesheet">
<style>
  :root {
    --backdrop: #1c1c1c;
    --card: #2b2b2c;
    --brand-blue: #3f6fb7;
    --white: #ffffff;
    --muted: #e6e6e6;
  }
  * { margin: 0; padding: 0; box-sizing: border-box; }
  html, body {
    width: 1200px; height: 1024px; overflow: hidden;
    background: var(--backdrop);
  }
  .canvas {
    width: 1200px; height: 1024px;
    display: flex; flex-direction: column; align-items: center; justify-content: center;
    gap: 40px;
  }
  .card {
    position: relative;
    width: 800px; height: 457px;
    background: var(--card);
    box-shadow: 0 10px 30px rgba(0,0,0,0.45);
  }

  /* Front */
  .card-front { display: flex; align-items: center; justify-content: center; }
  .wordmark {
    display: flex; align-items: center; gap: 16px;
    font-family: "Montserrat", sans-serif; font-weight: 700;
  }
  .wordmark-mark { width: 34px; height: 34px; }
  .card-front .wordmark { color: var(--white); font-size: 48px; }
  .card-front .wordmark-mark { background: var(--white); }

  /* Back */
  .card-back .wordmark {
    position: absolute; left: 70px; top: 150px;
    color: var(--brand-blue); font-size: 58px;
  }
  .card-back .wordmark-mark { background: var(--brand-blue); width: 40px; height: 40px; }

  .person {
    position: absolute; right: 62px; top: 92px; text-align: right;
    font-family: "Montserrat", sans-serif; color: var(--white);
  }
  .person-name { font-weight: 700; font-size: 22px; line-height: 1.1; }
  .person-title { font-weight: 600; font-size: 13px; letter-spacing: 0.3px; }

  .address {
    position: absolute; right: 62px; top: 218px; text-align: right;
    font-family: "Questrial", sans-serif; color: var(--muted);
    font-size: 19px; line-height: 1.4;
  }

  .contacts {
    position: absolute; left: 90px; bottom: 48px;
    list-style: none;
    font-family: "Questrial", sans-serif; color: var(--muted);
    font-size: 20px; line-height: 1.45;
  }
  .contacts li { display: flex; align-items: center; gap: 12px; }
  .contacts svg { width: 16px; height: 16px; fill: var(--brand-blue); flex: none; }
</style>
</head>
<body>
<main class="canvas">
  <section class="card card-front" aria-label="Card front">
    <div class="wordmark"><span class="wordmark-mark"></span>VelmoraNet</div>
  </section>

  <section class="card card-back" aria-label="Card back">
    <div class="wordmark"><span class="wordmark-mark"></span>VelmoraNet</div>

    <div class="person">
      <div class="person-name">Roshan Adeel</div>
      <div class="person-title">Managing Director</div>
    </div>

    <address class="address" style="font-style: normal;">
      Velmora Net Sdn. Bhd. 5th Floor, Block D<br>
      Wisma PLB, No.14 Jalan Seri Melor<br>
      50470, Kuala Lumpur Malaysia
    </address>

    <ul class="contacts">
      <li>
        <svg viewBox="0 0 16 16" aria-hidden="true"><path d="M3 1h3l1.5 3.5-2 1.3a8 8 0 0 0 4.7 4.7l1.3-2L15 10v3a2 2 0 0 1-2 2A12 12 0 0 1 1 3a2 2 0 0 1 2-2z"/></svg>
        603 XXX XXXX
      </li>
      <li>
        <svg viewBox="0 0 16 16" aria-hidden="true"><path d="M4 1h8v4H4zM1 6h14v6h-3v3H4v-3H1zm4 5v3h6v-3z"/></svg>
        603 XXX XXXX
      </li>
      <li>
        <svg viewBox="0 0 16 16" aria-hidden="true"><path d="M1 3h14v10H1zm1.5 1.2V5l5.5 4 5.5-4v-.8L8 8z"/></svg>
        info@velmoranet.com
      </li>
      <li>
        <svg viewBox="0 0 16 16" aria-hidden="true"><path d="M8 1a7 7 0 1 0 0 14A7 7 0 0 0 8 1zm0 1.5c-1 1.3-1.6 3.2-1.7 5H2.6A5.5 5.5 0 0 1 8 2.5zm0 0a5.5 5.5 0 0 1 5.4 5H9.7c-.1-1.8-.7-3.7-1.7-5zM2.6 8.5h3.7c.1 1.8.7 3.7 1.7 5a5.5 5.5 0 0 1-5.4-5zm7.1 0h3.7A5.5 5.5 0 0 1 8 13.5c1-1.3 1.6-3.2 1.7-5z"/></svg>
        www.velmoranet.com
      </li>
    </ul>
  </section>
</main>
</body>
</html>
```